Veltrane Group Business Card Design

The CEO is looking for a new trendy look for his business card.
You can stay with current branding or come up with something new/creative. It can be 3D, including Medical Office buildings. You can use our logo in a variety of colors. Please include name, title, company name, company website, email address, cell number

Target Market(s)

Real Estate Development and Construction

Industry/Entity Type

Health care real estate

Contact Information for Business Card

Rohesh Kamdar, CEO M-604.781.2249 E-roheshkamdar@veltrane.com Address:4180 Lindqvist Ave, Tampa, FL 33482 www.veltrane.com

Font styles to use
Other font styles liked:
• Be creative

Requirements
Must have
• Creative, trendy look
Nice to have
• Please go to our website to get a feel- www. veltrane.com
Should not have
• small fonts

```html
<!DOCTYPE html>
<html lang="en">
<head>
<meta charset="utf-8">
<title>Veltrane Group Business Card</title>
<link href="https://fonts.googleapis.com/css2?family=Lato:wght@400;700;900&display=swap" rel="stylesheet">
<style>
  :root {
    --bg: #2b2b2b;
    --brand-red: #b11f2b;
    --card-white: #ffffff;
    --ink: #1a1a1a;
    --shadow: rgba(0,0,0,0.45);
  }
  * { margin: 0; padding: 0; box-sizing: border-box; }
  html, body {
    width: 1200px; height: 694px; overflow: hidden;
    background: var(--bg);
    font-family: "Lato", Arial, sans-serif;
  }
  .stage {
    position: relative; width: 1200px; height: 694px;
    display: flex; align-items: center; justify-content: center; gap: 48px;
  }
  .card {
    position: relative;
    width: 540px; height: 310px;
    border-radius: 24px;
    box-shadow: 0 16px 36px var(--shadow);
    overflow: hidden;
  }
  .card--front {
    background: var(--brand-red);
    display: flex; align-items: center; justify-content: center;
  }
  .wordmark {
    font-weight: 900;
    letter-spacing: -0.5px;
    line-height: 1;
    white-space: nowrap;
  }
  .card--front .wordmark { color: var(--card-white); font-size: 64px; }
  .card--back { background: var(--card-white); }
  .card--back .brand-area {
    position: absolute; left: 0; top: 150px;
    width: 290px; padding-left: 28px;
  }
  .card--back .wordmark {
    color: var(--brand-red); font-size: 32px;
  }
  .divider {
    position: absolute; left: 290px; top: 40px;
    width: 2px; height: 230px;
    background: linear-gradient(to bottom, rgba(177,31,43,0.15), var(--brand-red) 40%, var(--brand-red) 70%, rgba(177,31,43,0.15));
  }
  .contact {
    position: absolute; left: 310px; top: 54px; right: 14px;
  }
  .contact__name {
    color: var(--brand-red); font-weight: 700; font-size: 28px; line-height: 1.1;
    white-space: nowrap;
  }
  .contact__title {
    color: var(--ink); font-size: 15px; margin: 4px 0 22px;
  }
  .contact__list { list-style: none; }
  .contact__item {
    display: flex; align-items: flex-start; gap: 9px;
    color: var(--ink); font-size: 14px; line-height: 1.25; margin-bottom: 9px;
    white-space: nowrap;
  }
  .contact__icon { width: 14px; height: 14px; flex: none; margin-top: 1px; fill: var(--brand-red); }
</style>
</head>
<body>
<main class="stage">
  <section class="card card--front" aria-label="Card front">
    <span class="wordmark">Veltrane Group</span>
  </section>

  <section class="card card--back" aria-label="Card back">
    <div class="brand-area">
      <span class="wordmark">Veltrane Group</span>
    </div>
    <div class="divider"></div>
    <div class="contact">
      <h1 class="contact__name">Rohesh Kamdar</h1>
      <p class="contact__title">CEO</p>
      <ul class="contact__list">
        <li class="contact__item">
          <svg class="contact__icon" viewBox="0 0 16 16" aria-hidden="true"><path d="M4 0h8a1.5 1.5 0 0 1 1.5 1.5v13A1.5 1.5 0 0 1 12 16H4a1.5 1.5 0 0 1-1.5-1.5v-13A1.5 1.5 0 0 1 4 0zm0.5 2v10.5h7V2zM8 13.2a.9.9 0 1 0 0 1.8.9.9 0 0 0 0-1.8z"/></svg>
          <span>604.781.2249</span>
        </li>
        <li class="contact__item">
          <svg class="contact__icon" viewBox="0 0 16 16" aria-hidden="true"><path d="M0 3h16v1.2L8 9 0 4.2zM0 6l8 4.8L16 6v7H0z"/></svg>
          <span>roheshkamdar@veltrane.com</span>
        </li>
        <li class="contact__item">
          <svg class="contact__icon" viewBox="0 0 16 16" aria-hidden="true"><path d="M8 0a8 8 0 1 0 0 16A8 8 0 0 0 8 0zm0 1.5c.8 0 1.8 1.6 2.2 4.5H5.8C6.2 3.1 7.2 1.5 8 1.5zM1.6 7.2h2.9a14 14 0 0 0 0 1.6H1.6a6.5 6.5 0 0 1 0-1.6zm4.1 0h4.6a13 13 0 0 1 0 1.6H5.7a13 13 0 0 1 0-1.6zm5.8 0h2.9a6.5 6.5 0 0 1 0 1.6h-2.9a14 14 0 0 0 0-1.6zM5.8 10h4.4c-.4 2.9-1.4 4.5-2.2 4.5S6.2 12.9 5.8 10z"/></svg>
          <span>www.veltrane.com</span>
        </li>
        <li class="contact__item">
          <svg class="contact__icon" viewBox="0 0 16 16" aria-hidden="true"><path d="M8 0a5.5 5.5 0 0 0-5.5 5.5C2.5 10 8 16 8 16s5.5-6 5.5-10.5A5.5 5.5 0 0 0 8 0zm0 7.6a2 2 0 1 1 0-4 2 2 0 0 1 0 4z"/></svg>
          <span>4180 Lindqvist Ave, Tampa,<br>FL 33482</span>
        </li>
      </ul>
    </div>
  </section>
</main>
</body>
</html>
```